Luxury Business Card Design for High-End Window Treatments

Gilded Slatworks
Custom Plantation Shutters & Architectural Shading Systems

⸻

BACK

Daniel Trevick
Owner

Custom Interior & Exterior Window Treatments

919-555-0148
gildedslatworks.com

I have included a picture that I’m hoping we can use on the back, but I’m also wondering if you can get rid of the ladder? Should we get rid of shutters , shades and blinds underneath Gilded Slatworks?

Target Market(s)

High-end residential homeowners, custom home builders, architects, interior designers, and luxury renovation clients seeking premium plantation shutters and motorized architectural shading systems.

Industry/Entity Type

Custom Window treatments

Contact Information for Business Card

Front Gilded Slatworks Custom Plantation Shutters Motorized Architectural Shading Systems BACK Daniel Trevick Owner 919-555-0148 GildedSlatworks.com Custom Interior & Exterior Window Treatments By Appointment

Requirements
Nice to have
• Not 100% sure on nice to halves or the color but you can definitely check out my website to get a better understanding of what I’m trying to do

```html
<!DOCTYPE html>
<html lang="en">
<head>
<meta charset="utf-8">
<title>Gilded Slatworks — Business Card</title>
<link href="https://fonts.googleapis.com/css2?family=Montserrat:wght@500;600;700&display=swap" rel="stylesheet">
<style>
  :root {
    --page-bg: #c4c4c4;
    --card-bg: #e8e2d8;
    --gold: #b8961a;
    --gold-soft: rgba(226, 196, 92, 0.22);
    --ink: #1c1c1c;
    --bar: #1e1e1e;
    --bar-text: #ffffff;
    --icon: #e2b93b;
    --photo-tone: #4f5963;
  }
  * { margin: 0; padding: 0; box-sizing: border-box; }
  html, body { width: 804px; height: 1200px; overflow: hidden; }
  body {
    background: var(--page-bg);
    font-family: "Montserrat", Arial, sans-serif;
    position: relative;
  }
  .card {
    position: absolute;
    left: 173px;
    width: 458px;
    height: 262px;
    background: var(--card-bg);
    overflow: hidden;
  }
  .card--front { top: 108px; }
  .card--back { top: 411px; }

  .wave {
    position: absolute;
    border-radius: 50%;
    background: radial-gradient(ellipse at center, var(--gold-soft), rgba(226,196,92,0) 70%);
  }

  .brand-title {
    position: absolute;
    left: 37px; top: 28px;
    font-weight: 700;
    font-size: 33px;
    line-height: 33px;
    color: var(--gold);
    letter-spacing: -0.5px;
    text-transform: uppercase;
  }
  .services {
    position: absolute;
    left: 37px; top: 117px;
    font-weight: 600;
    font-size: 14px;
    line-height: 16.5px;
    color: var(--ink);
  }
  .services .highlight { color: var(--gold); }

  .wordmark {
    position: absolute;
    left: 310px; top: 34px;
    width: 116px;
    text-align: center;
    color: var(--ink);
  }
  .wordmark__name {
    font-weight: 500;
    font-size: 19px;
    line-height: 22px;
  }
  .wordmark__tagline {
    margin-top: 6px;
    font-weight: 500;
    font-size: 8.5px;
    word-spacing: 5px;
  }

  .contact-bar {
    position: absolute;
    left: 38px; top: 194px;
    width: 382px; height: 38px;
    background: var(--bar);
    color: var(--bar-text);
    display: flex;
    align-items: center;
    font-weight: 500;
    font-size: 14px;
  }
  .contact-bar__item {
    display: flex;
    align-items: center;
    gap: 7px;
  }
  .contact-bar__item--phone { margin-left: 28px; }
  .contact-bar__divider {
    width: 1px; height: 17px;
    background: var(--bar-text);
    margin: 0 30px 0 34px;
  }
  .contact-bar svg { flex: none; }

  .back-title {
    position: absolute;
    left: 37px; top: 31px;
    font-weight: 700;
    font-size: 20px;
    line-height: 22.5px;
    color: var(--gold);
    text-transform: uppercase;
  }
  .back-lede {
    position: absolute;
    left: 37px; top: 87px;
    font-weight: 600;
    font-size: 16px;
    line-height: 16.5px;
    color: var(--ink);
  }
  .person-name {
    position: absolute;
    left: 37px; top: 164px;
    font-weight: 600;
    font-size: 17.5px;
    color: var(--gold);
  }
  .project-photo {
    position: absolute;
    left: 258px; top: 34px;
    width: 161px; height: 133px;
    border: 1px solid var(--gold);
    background: var(--photo-tone);
  }
</style>
</head>
<body>

  <section class="card card--front">
    <div class="wave" style="left:230px; top:100px; width:260px; height:110px;" role="img" aria-label="Faint gold flowing line pattern"></div>
    <div class="wave" style="left:-40px; top:190px; width:200px; height:90px;" role="img" aria-label="Faint gold flowing line pattern"></div>

    <h1 class="brand-title">Gilded<br>Slatworks</h1>

    <p class="services">
      <span class="highlight">Custom Plantation Shutters</span><br>
      Motorized Architectural<br>
      Shading Systems
    </p>

    <div class="wordmark">
      <div class="wordmark__name">Gilded<br>Slatworks</div>
      <div class="wordmark__tagline">Shutters Shades Blinds</div>
    </div>

    <div class="contact-bar">
      <span class="contact-bar__item contact-bar__item--phone">
        <svg width="10" height="10" viewBox="0 0 24 24"><path fill="var(--icon)" d="M6.6 10.8a15.1 15.1 0 0 0 6.6 6.6l2.2-2.2a1 1 0 0 1 1-.25 11.4 11.4 0 0 0 3.6.57 1 1 0 0 1 1 1V20a1 1 0 0 1-1 1A17 17 0 0 1 3 4a1 1 0 0 1 1-1h3.5a1 1 0 0 1 1 1c0 1.25.2 2.45.57 3.57a1 1 0 0 1-.25 1z"/></svg>
        919 555 0148
      </span>
      <span class="contact-bar__divider"></span>
      <span class="contact-bar__item">
        <svg width="9" height="10" viewBox="0 0 20 22"><path fill="var(--icon)" d="M2 1l16 9-7 1.5L7.5 20z"/></svg>
        gildedslatworks.com
      </span>
    </div>
  </section>

  <section class="card card--back">
    <div class="wave" style="left:360px; top:-20px; width:140px; height:260px;" role="img" aria-label="Faint gold flowing line pattern"></div>
    <div class="wave" style="left:-40px; top:190px; width:200px; height:90px;" role="img" aria-label="Faint gold flowing line pattern"></div>

    <h2 class="back-title">Custom Interior<br>and Exterior</h2>

    <p class="back-lede">Window Treatments<br>By Appointment</p>

    <div class="project-photo" role="img" aria-label="Photo of a home's covered porch fitted with exterior motorized shades"></div>

    <p class="person-name">Daniel Trevick</p>

    <div class="contact-bar">
      <span class="contact-bar__item contact-bar__item--phone">
        <svg width="10" height="10" viewBox="0 0 24 24"><path fill="var(--icon)" d="M6.6 10.8a15.1 15.1 0 0 0 6.6 6.6l2.2-2.2a1 1 0 0 1 1-.25 11.4 11.4 0 0 0 3.6.57 1 1 0 0 1 1 1V20a1 1 0 0 1-1 1A17 17 0 0 1 3 4a1 1 0 0 1 1-1h3.5a1 1 0 0 1 1 1c0 1.25.2 2.45.57 3.57a1 1 0 0 1-.25 1z"/></svg>
        919 555 0148
      </span>
      <span class="contact-bar__divider"></span>
      <span class="contact-bar__item">
        <svg width="9" height="10" viewBox="0 0 20 22"><path fill="var(--icon)" d="M2 1l16 9-7 1.5L7.5 20z"/></svg>
        gildedslatworks.com
      </span>
    </div>
  </section>

</body>
</html>
```